Stonebridge Building and Projects business cards

A business card with watermark background (construction work)

Company logo attached

Home improvement projects
House renovations
Bathroom and kitchen renovations
House extensions
New builds and granny flats

Director Omar Haddani
(Phone number)
omar@sbpbuilding.com.au
(Instagram logo) sbp_building

```html
<!DOCTYPE html>
<html lang="en">
<head>
<meta charset="utf-8">
<title>Stonebridge Building and Projects – Business Cards</title>
<link href="https://fonts.googleapis.com/css2?family=Montserrat:wght@500;700&family=Arimo:wght@400&display=swap" rel="stylesheet">
<style>
  :root {
    --brand-blue: #2f78b9;
    --ink: #3a3a3a;
    --muted: #555555;
    --paper: #ffffff;
    --stage: #2a2a2a;
  }
  html, body {
    margin: 0;
    padding: 0;
    width: 1200px;
    height: 900px;
    overflow: hidden;
    background: var(--stage);
  }
  .canvas {
    position: relative;
    width: 1200px;
    height: 900px;
  }
  .card {
    position: absolute;
    width: 600px;
    height: 343px;
    box-sizing: border-box;
    box-shadow: 0 12px 30px rgba(0,0,0,0.5);
  }
  /* Front card */
  .card--front {
    left: 110px;
    top: 70px;
    background: var(--paper);
    border-bottom: 4px solid var(--brand-blue);
    display: flex;
  }
  .front__brand {
    width: 50%;
    display: flex;
    align-items: center;
    justify-content: center;
    gap: 10px;
    padding: 0 24px;
    box-sizing: border-box;
  }
  .brand-mark {
    width: 14px;
    height: 14px;
    background: var(--brand-blue);
    flex: none;
  }
  .brand-name {
    font-family: "Montserrat", sans-serif;
    font-weight: 700;
    font-size: 22px;
    line-height: 1.2;
    color: var(--brand-blue);
    margin: 0;
  }
  .front__divider {
    width: 1px;
    margin: 30px 0;
    background: linear-gradient(to bottom, rgba(0,0,0,0), rgba(0,0,0,0.25), rgba(0,0,0,0));
  }
  .front__contact {
    width: 50%;
    padding: 70px 20px 0 34px;
    box-sizing: border-box;
  }
  .person-name {
    font-family: "Montserrat", sans-serif;
    font-weight: 700;
    font-size: 24px;
    color: var(--brand-blue);
    margin: 0;
  }
  .person-role {
    font-family: "Arimo", sans-serif;
    font-size: 15px;
    color: var(--muted);
    margin: 2px 0 16px;
  }
  .contact-list {
    list-style: none;
    margin: 0;
    padding: 0;
    font-family: "Arimo", sans-serif;
    font-size: 13.5px;
    color: var(--ink);
  }
  .contact-list li {
    display: flex;
    align-items: center;
    gap: 8px;
    margin-bottom: 6px;
  }
  .contact-list li.social { margin-top: 12px; }
  .contact-icon { width: 14px; height: 14px; flex: none; }
  .social-square {
    width: 16px;
    height: 16px;
    border-radius: 3px;
    background: var(--brand-blue);
    flex: none;
  }
  .web-accent { color: var(--brand-blue); }

  /* Back card */
  .card--back {
    left: 490px;
    top: 487px;
    background: var(--brand-blue);
    color: var(--paper);
    display: flex;
    flex-direction: column;
    align-items: center;
    justify-content: center;
    text-align: center;
    padding: 0 40px;
  }
  .card--back .brand-name {
    color: var(--paper);
    font-size: 28px;
  }
  .card--back .brand-mark { background: var(--paper); width: 16px; height: 16px; }
  .back__brand {
    display: flex;
    align-items: center;
    gap: 12px;
    margin-bottom: 40px;
  }
  .services {
    font-family: "Arimo", sans-serif;
    font-size: 17px;
    line-height: 1.35;
    margin: 0;
  }
</style>
</head>
<body>
<main class="canvas">
  <section class="card card--front" aria-label="Business card front">
    <div class="front__brand">
      <span class="brand-mark"></span>
      <p class="brand-name">Stonebridge Building and Projects</p>
    </div>
    <div class="front__divider"></div>
    <div class="front__contact">
      <h1 class="person-name">Omar Haddani</h1>
      <p class="person-role">Director</p>
      <ul class="contact-list">
        <li>
          <svg class="contact-icon" viewBox="0 0 16 16" aria-hidden="true"><path d="M3 1.5l3 3-1.6 1.8c.8 1.8 2.3 3.3 4.3 4.3L10.5 9l3 3-2 2.5C6 14 2 10 1.5 4.5z" fill="#2f78b9"/></svg>
          041-555 302 118
        </li>
        <li>
          <svg class="contact-icon" viewBox="0 0 16 16" aria-hidden="true"><rect x="1" y="3" width="14" height="10" fill="#2f78b9"/><path d="M1 3l7 6 7-6" stroke="#fff" stroke-width="1.3" fill="none"/></svg>
          omar@sbpbuilding.com.au
        </li>
        <li>
          <svg class="contact-icon" viewBox="0 0 16 16" aria-hidden="true"><circle cx="8" cy="8" r="6.5" fill="none" stroke="#2f78b9" stroke-width="1.4"/><ellipse cx="8" cy="8" rx="2.8" ry="6.5" fill="none" stroke="#2f78b9" stroke-width="1.2"/><path d="M1.5 8h13M2.8 4.5h10.4M2.8 11.5h10.4" stroke="#2f78b9" stroke-width="1.1"/></svg>
          <span>www.<span class="web-accent">sbpbuilding</span>.com.au</span>
        </li>
        <li class="social">
          <span class="social-square"></span>
          sbp_building
        </li>
      </ul>
    </div>
  </section>

  <section class="card card--back" aria-label="Business card back">
    <div class="back__brand">
      <span class="brand-mark"></span>
      <p class="brand-name">Stonebridge Building and Projects</p>
    </div>
    <p class="services">
      Home improvement projects&nbsp; | House renovations<br>
      Bathroom and kitchen renovations<br>
      House extensions | &nbsp;New builds and granny flats
    </p>
  </section>
</main>
</body>
</html>
```